New Website Announcement

We need a flyer to announce our new website to customers and prospective clients. The website will be launching soon, but I can provide a detailed outline in PDF form with copy and imagery to serve as inspiration for this design.

I would like a postcard size document that can be mailed in an envelope (no need for postcard style mailer info on 1 side)

About my company:

Verity Lane Studio is a new breed of marketing consulting agency built for the next frontier of consumer learning. Social interaction will be at the heart of great insights going forward – in how consumers engage with brands and in how organizations socialize what they learn to gain competitive advantage.
By fusing innovative insights techniques, technology and compelling graphic design-based reporting, we ensure results get noticed and make an impact.

contact info that can also be included:

Email: marek@veritylane-studio.net

Phone: 518-732-5164

Thanks

Attention all designers submitting a design for this project. Please keep in mind a few important details about this project.

1. Remember that the main objective of this postcard is to announce my new website.

2. Please be sure to read the brief for the copy I would like on each side. You can be creative in how it is displayed, but I need this key information somewhere. All other copy on the attached files is for your background only.

3. Please do not submit overly simple designs that just take the images I provided and overlay a text box with my copy. I could easily do this myself in PowerPoint in 5 minutes.

4. Remember that the design should be edgy and modern but needs to be professional and speak to a business audience.

Please submit any questions. Thank you for your submissions. 

Marek

Target Market(s)

senior level marketing and research clients at large companies and agencies

Industry/Entity Type

Marketing

Requirements
Must have
• Main message:

Need an engaging way to tell customers and prospective clients that we have a new website and that they should come visit us online to learn more about out services, check out case studies and read about our exciting partnerships.

COPY TO USE - UPDATED

Side 1:
(logo)
Introducing Verity Lane Studio

Let’s talk about taking research out of the dark ages.

Visit our newly launched website to learn how and get in touch.

www.veritylane-studio.net

Side 2
Logo
followed by tagline:
Consumer insights that get noticed.
A leading-edge marketing partnership that really works.

Additional text to use on Side 2:
How we can help...

Think of us as your go-to resource for identifying and incorporating the most innovative and exciting techniques into your research programs. We carefully curate and develop close partnerships with the best of the best - from online qualitative research and mobile ethnography to social media listening and fresh takes on concept testing, we can guide the way.

Plus, we believe that socializing consumer learning is just as critical as gathering it.By taking insights deliverables to the next level – through infographics, videos, magazines,interactive profiles and so much more – we are getting stakeholders excited to engage with research and inspired to take action because of it.
It’s a new way to look at insights from a new type of partner. And, it’s a new way to get the most from your research dollars.
Nice to have
• could incorporate our website main image of the lamp on white brick background which is attached, but not 100% mandatory.
Should not have
• - should not be too playful or young, but needs to be modern and design focused

- should not be cluttered or overly 'salesy'

- needs to be upscale and elegant / compelling and aligned with the look and feel of the website imagery (see attached)

```html
<!DOCTYPE html>
<html lang="en">
<head>
<meta charset="utf-8">
<title>Verity Lane Studio – Postcard</title>
<link rel="stylesheet" href="https://fonts.googleapis.com/css2?family=Open+Sans:wght@400;600;700&family=PT+Sans+Narrow&display=swap">
<style>
  :root {
    --page: #ffffff;
    --card: #ffffff;
    --brand-blue: #2f6fba;
    --logo-blue: #1b7fc9;
    --ink: #111111;
    --text: #1c1c1c;
    --bar: #111111;
    --rule: #d6d6d6;
    --brick-light: #f1f1f1;
    --brick-mid: #d2d2d2;
  }
  * { box-sizing: border-box; margin: 0; padding: 0; }
  html, body { width: 1200px; height: 882px; overflow: hidden; background: var(--page); }
  .postcard {
    position: absolute; left: 30px; top: 30px; width: 1138px; height: 820px;
    background: var(--card);
    box-shadow: 0 0 10px rgba(0,0,0,.45);
    overflow: hidden;
  }
  .header-wall {
    position: absolute; left: 0; top: 0; width: 100%; height: 280px;
    background:
      linear-gradient(180deg, rgba(255,255,255,0) 0%, rgba(255,255,255,.55) 40%, rgba(255,255,255,.4) 75%, rgba(150,150,150,.5) 100%),
      linear-gradient(90deg, var(--brick-mid), var(--brick-light) 30%, var(--brick-mid) 55%, var(--brick-light) 80%, var(--brick-mid));
  }
  .header-rule {
    position: absolute; left: 0; top: 63px; width: 100%; height: 13px; background: var(--bar);
  }
  .brand-name {
    position: absolute; left: 82px; top: 106px;
    font-family: 'Open Sans', sans-serif; font-weight: 700;
    font-size: 46px; line-height: 52px; color: var(--logo-blue);
  }
  .tagline {
    position: absolute; left: 401px; top: 142px;
    font-family: 'PT Sans Narrow', sans-serif; font-size: 32px; line-height: 39px; color: var(--ink);
  }
  .section-title {
    position: absolute; left: 79px;
    font-family: 'Open Sans', sans-serif; font-weight: 600; font-size: 39px; color: var(--brand-blue);
    line-height: 1;
  }
  .help-title { top: 299px; }
  .focus-title { top: 594px; }
  .help-copy {
    position: absolute; left: 79px; top: 345px; width: 983px;
    font-family: 'Open Sans', sans-serif; font-size: 16.4px; line-height: 24.7px;
    letter-spacing: .8px; color: var(--text); text-align: justify;
  }
  .focus-list { list-style: none; }
  .focus-item {
    position: absolute; top: 660px; text-align: center;
    font-family: 'PT Sans Narrow', sans-serif; font-size: 22px; line-height: 26px; color: var(--ink);
    transform: translateX(-50%); white-space: nowrap;
  }
  .focus-item svg { display: block; margin: 0 auto 8px; width: 56px; height: 56px; }
  .launch-note {
    position: absolute; left: 79px; right: 76px; top: 770px;
    padding-top: 10px; border-top: 1px solid var(--rule);
    display: flex; justify-content: space-between;
    font-family: 'Open Sans', sans-serif; font-size: 15px; line-height: 20px; color: var(--text);
  }
  .launch-note strong { color: var(--brand-blue); font-weight: 700; }
</style>
</head>
<body>
<div class="postcard">
  <header>
    <div class="header-wall" role="img" aria-label="White painted brick wall photograph"></div>
    <div class="header-rule"></div>
    <div class="brand-name">Verity Lane<br>Studio</div>
    <p class="tagline">Consumer insights that get noticed.<br>A leading-edge marketing partnership that really works</p>
  </header>

  <h2 class="section-title help-title">How we can help…</h2>
  <div class="help-copy">
    <p>Think of us as your go-to resource for identifying and incorporating the most innovative and exciting techniques into your research programs. We carefully curate and develop close partnerships with the best of the best - from online qualitative research and mobile ethnography to social media listening and fresh takes on concept testing, we can guide the way.</p>
    <p>Plus, we believe that socializing consumer learning is just as critical as gathering it. By taking insights deliverables to the next level – through infographics, videos, magazines, interactive profiles and so much more – we are getting stakeholders excited to engage with research and inspired to take action because of it.</p>
    <p>It’s a new way to look at insights from a new type of partner. And, it’s a new way to get the most from your research dollars.</p>
  </div>

  <h2 class="section-title focus-title">We focus on designing the…</h2>
  <ul class="focus-list">
    <li class="focus-item" style="left:180px">
      <svg viewBox="0 0 58 58"><circle cx="22" cy="22" r="16" fill="none" stroke="#111" stroke-width="5"/><line x1="34" y1="34" x2="50" y2="50" stroke="#111" stroke-width="8" stroke-linecap="round"/></svg>
      best research approach
    </li>
    <li class="focus-item" style="left:410px">
      <svg viewBox="0 0 58 58"><path d="M2 18h12l8-4h10l8 5h16v18h-8l-14 12h-10l-14-12h-8z" fill="#111"/><path d="M20 24l10 6 8-5" fill="none" stroke="#fff" stroke-width="2.2"/><path d="M24 40l4 4M30 38l4 4M36 36l3 3" stroke="#fff" stroke-width="1.8"/></svg>
      most flexible partnership
    </li>
    <li class="focus-item" style="left:642px">
      <svg viewBox="0 0 58 58"><rect x="4" y="40" width="7" height="16" fill="#111"/><rect x="14" y="34" width="7" height="22" fill="#111"/><rect x="24" y="38" width="7" height="18" fill="#111"/><rect x="34" y="30" width="7" height="26" fill="#111"/><rect x="44" y="24" width="7" height="32" fill="#111"/><polyline points="7,30 17,22 27,26 37,14 48,8" fill="none" stroke="#111" stroke-width="2.5"/><circle cx="48" cy="8" r="3.5" fill="#111"/><circle cx="37" cy="14" r="3" fill="#111"/></svg>
      most impactful analysis
    </li>
    <li class="focus-item" style="left:923px">
      <svg viewBox="0 0 58 58"><path d="M4 12h18l4 5h28v37H4z" fill="none" stroke="#111" stroke-width="4"/><path d="M29 46l-10-10a5.5 5.5 0 0 1 10-6a5.5 5.5 0 0 1 10 6z" fill="#111"/></svg>
      most elegant, compelling deliverables
    </li>
  </ul>

  <footer class="launch-note">
    <span><strong>Our new website is live</strong> – visit www.veritylane-studio.net to learn more</span>
    <span>marek@veritylane-studio.net &nbsp;|&nbsp; 518-732-5164</span>
  </footer>
</div>
</body>
</html>
```